Harborview Optical -Window Poster (Optometrist)

We are an optometry practice and we need a poster for a new store promotion for our window highlighting we now also sell 2 pairs of glasses as a package deal. The size will be 1300mm width x 1900mm height

The artwork will be displayed as a fabric banner in our shop window. We have 7 other banners with different services our business provides. The words needs to standout for passers by and the cars stopped at the traffic lights out front of our business. We already have signs with our logos phone number etc. so we won't need them included in the poster.

It would need to include the following information.

Two pair packages now available*

*Conditions apply

The artwork will be displayed as a fabric banner in our shop window. We have 7 other banners with different services our business provides. The words needs to standout for passers by and the cars stopped at the traffic lights out front of our business. We already have signs with our logos phone number etc. so we won't need them included in the poster. Thank you for your work it's amazing Added Saturday, February 18, 2017

The artwork will be displayed as a fabric banner in our shop window. We have 7 other banners with different services our business provides. The words needs to standout for passers by and the cars stopped at the traffic lights out front of our business. We already have signs with our logos phone number etc. so we won't need them included in the poster. Added Saturday, February 18, 2017

Target Market(s)

Cars driving past and stopped at traffic lights outside our store.

Industry/Entity Type

Optician

Requirements
Must have
• Poster must say:
• Two pair packages now available*
• *Conditions apply

```html
<!DOCTYPE html>
<html lang="en">
<head>
<meta charset="utf-8">
<title>Harborview Optical – Two Pair Packages Window Poster</title>
<link rel="stylesheet" href="https://fonts.googleapis.com/css2?family=Archivo+Black&family=Cinzel:wght@700&family=Yellowtail&display=swap">
<style>
  :root {
    --sky-deep: #263f86;
    --sky-mid: #1f58a8;
    --sky-light: #5c8ed0;
    --haze: #eef0fa;
    --headline-grey: #d3d6dc;
    --headline-yellow: #f1c81a;
    --shadow-ink: #111111;
    --script-white: #ffffff;
    --script-shade: #9aa3ad;
    --rule-navy: #1e5a98;
    --label-white: #ffffff;
    --label-ink: #000000;
  }
  html, body {
    margin: 0;
    padding: 0;
    width: 962px;
    height: 1200px;
    overflow: hidden;
    background: #ffffff;
  }
  .poster {
    position: relative;
    width: 962px;
    height: 1200px;
    overflow: hidden;
    background:
      radial-gradient(ellipse 70% 55% at 25% 100%, rgba(240,240,250,0.95) 0%, rgba(200,200,235,0.5) 45%, rgba(120,120,180,0) 75%),
      radial-gradient(ellipse 60% 40% at 80% 100%, rgba(238,240,250,0.95) 0%, rgba(160,180,230,0.4) 55%, rgba(90,140,210,0) 80%),
      linear-gradient(100deg, var(--sky-deep) 0%, var(--sky-mid) 45%, var(--sky-light) 100%);
  }
  .poster__clouds {
    position: absolute;
    top: 0;
    height: 120px;
  }
  .poster__clouds--left {
    left: 0;
    width: 280px;
    background: radial-gradient(ellipse 60% 45% at 40% 30%, rgba(235,238,248,0.9) 0%, rgba(200,215,240,0.5) 45%, rgba(80,130,200,0) 80%);
  }
  .poster__clouds--right {
    right: 0;
    width: 230px;
    background: radial-gradient(ellipse 60% 55% at 65% 45%, rgba(235,240,250,0.9) 0%, rgba(190,215,245,0.5) 45%, rgba(80,140,210,0) 80%);
  }
  .poster__art {
    position: absolute;
    inset: 0;
  }
  .script-line {
    font-family: "Yellowtail", cursive;
    font-size: 120px;
  }
  .headline {
    font-family: "Archivo Black", sans-serif;
  }
  .conditions {
    font-family: "Cinzel", serif;
    font-weight: 700;
    font-size: 44px;
  }
</style>
</head>
<body>
<main class="poster">
  <div class="poster__clouds poster__clouds--left" role="img" aria-label="Soft white clouds in the sky"></div>
  <div class="poster__clouds poster__clouds--right" role="img" aria-label="Soft white clouds in the sky"></div>

  <svg class="poster__art" width="962" height="1200" viewBox="0 0 962 1200" xmlns="http://www.w3.org/2000/svg">
    <defs>
      <linearGradient id="rule-glow" x1="0" x2="1" y1="0" y2="0">
        <stop offset="0" stop-color="#ffffff" stop-opacity="0"/>
        <stop offset="0.5" stop-color="#ffffff" stop-opacity="0.95"/>
        <stop offset="1" stop-color="#ffffff" stop-opacity="0"/>
      </linearGradient>
    </defs>

    <!-- Now available -->
    <g class="script-line">
      <text x="161" y="261" fill="var(--script-shade)" textLength="690" lengthAdjust="spacingAndGlyphs">Now Available*</text>
      <text x="158" y="258" fill="var(--script-white)" textLength="690" lengthAdjust="spacingAndGlyphs">Now Available*</text>
    </g>

    <rect class="rule rule--glow" x="215" y="288" width="515" height="3" fill="url(#rule-glow)"/>

    <!-- Headline -->
    <text class="headline headline--top" x="155" y="524" font-size="140" fill="var(--headline-grey)" textLength="693" lengthAdjust="spacingAndGlyphs">TWO PAIR</text>

    <g class="headline headline--main" font-size="158">
      <text x="164" y="671" fill="var(--shadow-ink)" textLength="708" lengthAdjust="spacingAndGlyphs">PACKAGES</text>
      <text x="158" y="664" fill="var(--headline-yellow)" textLength="708" lengthAdjust="spacingAndGlyphs">PACKAGES</text>
    </g>

    <rect class="rule rule--navy" x="213" y="701" width="604" height="3" fill="var(--rule-navy)"/>

    <!-- Conditions label -->
    <rect class="label" x="328" y="943" width="634" height="78" fill="var(--label-white)"/>
    <text class="conditions" x="334" y="996" fill="var(--label-ink)" textLength="604" lengthAdjust="spacingAndGlyphs">*Conditions apply</text>
  </svg>
</main>
</body>
</html>
```